Verdant Systems Business Card

want the back of card to be blue- with the logo in the center
front of card- info plus logo (info being mailing address, email address, and website address )
4 different names with titles to have on cards
1) Calvin Borsted - Owner
2) Naomi Trelvik- Customer Relationship Specialist
3) Felix Andrade- Vice President of Sales
4) Owen Markby- Chief Technology Officer

Target Market(s)

tech company in the government/probation office industry

Industry/Entity Type

Government Office

Contact Information for Business Card

1) Calvin Borsted - Owner

Colors
0355a3
ffffff

Requirements
Must have
• back side should be blue, with the logo placed in the center
• front side needs to include both the logo, as well as company info (info should include website address, email address, and mailing address)

```html
<!DOCTYPE html>
<html lang="en">
<head>
<meta charset="utf-8">
<title>Verdant Systems Business Card</title>
<link rel="stylesheet" href="https://fonts.googleapis.com/css2?family=PT+Serif&family=Roboto:wght@400&display=swap">
<style>
  :root {
    --navy: #28385f;
    --navy-ink: #2a3a66;
    --paper: #f7f7f7;
    --ground: #aaa7a8;
    --grey-text: #6d6f78;
    --white: #ffffff;
  }
  * { margin: 0; padding: 0; box-sizing: border-box; }
  html, body { width: 1200px; height: 1200px; overflow: hidden; }
  body { background: var(--ground); position: relative; font-family: "Roboto", sans-serif; }

  .card { position: absolute; width: 712px; height: 418px; border-radius: 24px; overflow: hidden; }
  .card-back { left: 238px; top: 118px; background: var(--navy); }
  .card-front { left: 231px; top: 644px; background: var(--paper); }

  .wordmark { position: absolute; font-family: "PT Serif", serif; font-weight: 400; text-align: center; text-transform: uppercase; line-height: 1; }
  .wordmark .word-main { display: block; }
  .wordmark .word-sub { display: block; }

  .card-back .wordmark { left: 0; right: 0; top: 136px; color: var(--white); }
  .card-back .word-main { font-size: 84px; letter-spacing: 2px; }
  .card-back .word-sub { font-size: 40px; letter-spacing: 13px; margin-top: 8px; }

  .card-front .wordmark { left: 390px; width: 300px; top: 138px; color: var(--navy-ink); }
  .card-front .word-main { font-size: 46px; letter-spacing: 1px; }
  .card-front .word-sub { font-size: 22px; letter-spacing: 7px; margin-top: 6px; }

  .edge-tab { position: absolute; left: -22px; top: 58px; width: 34px; height: 54px; border-radius: 0 27px 27px 0; background: var(--navy-ink); }

  .person { position: absolute; left: 37px; top: 72px; }
  .person-name { font-family: "PT Serif", serif; font-size: 23px; letter-spacing: 1px; color: var(--navy-ink); text-transform: uppercase; }
  .person-title { font-size: 17px; color: var(--grey-text); margin-top: 6px; }

  .address { position: absolute; left: 37px; top: 246px; font-size: 17px; line-height: 29px; color: var(--grey-text); }
  .contacts { position: absolute; left: 37px; top: 308px; list-style: none; }
  .contacts li { display: flex; align-items: center; font-size: 17px; line-height: 26px; color: var(--grey-text); }
  .contacts svg { width: 16px; height: 16px; margin-right: 14px; fill: var(--navy-ink); }
</style>
</head>
<body>
  <section class="card card-back" aria-label="Card back">
    <div class="wordmark"><span class="word-main">Verdant</span><span class="word-sub">Systems</span></div>
  </section>

  <section class="card card-front" aria-label="Card front">
    <div class="edge-tab"></div>
    <div class="person">
      <p class="person-name">Naomi Trelvik</p>
      <p class="person-title">Customer Relationship Specialist</p>
    </div>
    <div class="wordmark"><span class="word-main">Verdant</span><span class="word-sub">Systems</span></div>
    <p class="address">418 Cedarline Rd., Fenwick,<br>Lakeport, US 204871</p>
    <ul class="contacts">
      <li><svg viewBox="0 0 16 16"><path d="M1 5c0-2 3-3 7-3s7 1 7 3v1h-4V5H5v1H1z"/><path d="M4 7h8l2 7H2z"/></svg>555-014-2291</li>
      <li><svg viewBox="0 0 16 16"><path d="M1 3h14v1L8 9 1 4z"/><path d="M1 6l7 5 7-5v7H1z"/></svg>naomi.t@verdantsystems.com</li>
      <li><svg viewBox="0 0 16 16"><circle cx="8" cy="8" r="7"/><path d="M1 8h14M8 1c-3 4-3 10 0 14M8 1c3 4 3 10 0 14" stroke="#f7f7f7" stroke-width="1" fill="none"/></svg>www.verdantsystems.com</li>
    </ul>
  </section>
</body>
</html>
```